Home Security Company Business Card

Looking for a eye catching business card that is non traditional and stands out but yet still looks professional. It should include all the pertinent information such as name, title, address, telephone, e-mail, website address should definitely stand out and then finally the logo.

Target Market(s)

Residential and Commercial accounts mostly upscale accounts

Industry/Entity Type

Security

Contact Information for Business Card

Name
Title
Address
Office #
Cell #
E-mail
Website

Font styles to use
Serif
Sans Serif

Requirements
Must have
• Logo, two sided color configuration
Nice to have
• You decide
Should not have
• There really aren't any.

```html
<!DOCTYPE html>
<html lang="en">
<head>
<meta charset="utf-8">
<title>Bastion Guard Systems – Business Card</title>
<link href="https://fonts.googleapis.com/css2?family=Open+Sans:wght@400;600;700&display=swap" rel="stylesheet">
<style>
  :root {
    --maroon: #8e1b25;
    --maroon-dark: #5e0f16;
    --maroon-light: #b0343d;
    --gold: #e8b84a;
    --gold-light: #f6d77f;
    --gold-dark: #c98f24;
    --white: #ffffff;
    --stage: #ecebe8;
    --ink-gold: #7a2a10;
  }
  * { margin: 0; padding: 0; box-sizing: border-box; }
  html, body { width: 1200px; height: 913px; overflow: hidden; }
  body {
    background: var(--stage);
    font-family: "Open Sans", Arial, sans-serif;
    position: relative;
  }
  .card {
    position: absolute;
    top: 307px;
    width: 520px;
    height: 298px;
    border-radius: 18px;
    overflow: hidden;
    box-shadow: 0 6px 18px rgba(0,0,0,0.18);
  }
  .card--front { left: 50px; }
  .card--back { left: 630px; background: var(--white); }
  .card__art { position: absolute; inset: 0; width: 100%; height: 100%; }

  .brand {
    position: absolute;
    display: flex;
    align-items: center;
    gap: 8px;
    font-weight: 600;
    letter-spacing: 0.5px;
    text-transform: uppercase;
  }
  .brand__dot { border-radius: 50%; flex: none; }
  .card--front .brand { left: 34px; top: 118px; color: var(--white); font-size: 12px; line-height: 1.25; }
  .card--front .brand__dot { width: 22px; height: 22px; background: var(--gold); }
  .card--back .brand { left: 120px; top: 112px; color: var(--maroon); font-size: 20px; line-height: 1.2; }
  .card--back .brand__dot { width: 34px; height: 34px; background: var(--maroon); }

  .person { position: absolute; left: 282px; top: 40px; }
  .person__name { color: var(--white); font-size: 21px; font-weight: 700; line-height: 1.3; }
  .person__title { color: var(--gold); font-size: 13px; line-height: 1.3; }

  .contact { position: absolute; left: 282px; top: 94px; list-style: none; }
  .contact__item {
    display: flex; align-items: center; gap: 8px;
    color: var(--white); font-size: 13px; line-height: 20px;
  }
  .contact__icon { width: 12px; height: 12px; fill: var(--gold); flex: none; }

  .address {
    position: absolute; right: 36px; bottom: 30px;
    color: var(--ink-gold); font-size: 14px; font-weight: 600;
  }

  .website {
    position: absolute; left: 0; right: 0; top: 210px;
    text-align: center; color: var(--maroon);
    font-size: 16px; font-weight: 700;
  }
</style>
</head>
<body>

<section class="card card--front" aria-label="Card front">
  <svg class="card__art" viewBox="0 0 520 298" preserveAspectRatio="none" aria-hidden="true">
    <defs>
      <linearGradient id="maroonFill" x1="0" y1="0" x2="1" y2="1">
        <stop offset="0" stop-color="var(--maroon-light)"/>
        <stop offset="0.5" stop-color="var(--maroon)"/>
        <stop offset="1" stop-color="var(--maroon-dark)"/>
      </linearGradient>
      <linearGradient id="goldFill" x1="0" y1="0" x2="0" y2="1">
        <stop offset="0" stop-color="var(--gold-light)"/>
        <stop offset="0.5" stop-color="var(--gold)"/>
        <stop offset="1" stop-color="var(--gold-dark)"/>
      </linearGradient>
    </defs>
    <rect class="front-base" width="520" height="298" fill="url(#maroonFill)"/>
    <path class="front-stripe" d="M0 222 C120 246 200 192 300 182 C400 172 460 168 520 164 L520 298 L0 298 Z" fill="var(--white)"/>
    <path class="front-wave" d="M0 234 C120 258 205 206 305 196 C405 186 462 182 520 178 L520 298 L0 298 Z" fill="url(#goldFill)"/>
  </svg>

  <div class="brand"><span class="brand__dot"></span><span>Bastion Guard<br>Systems Inc.</span></div>

  <div class="person">
    <p class="person__name">Martin Halloway</p>
    <p class="person__title">Owner</p>
  </div>

  <ul class="contact">
    <li class="contact__item">
      <svg class="contact__icon" viewBox="0 0 12 12" aria-hidden="true"><path d="M1 4 C1 2 3 1 6 1 C9 1 11 2 11 4 L9 5 L8 3.5 L4 3.5 L3 5 Z M2.5 6 L9.5 6 L10.5 11 L1.5 11 Z"/></svg>
      <span>+555 2460-1180</span>
    </li>
    <li class="contact__item">
      <svg class="contact__icon" viewBox="0 0 12 12" aria-hidden="true"><path d="M2 1 L4.5 1 L5.5 3.8 L4 5 C4.8 6.6 5.6 7.4 7 8 L8.2 6.5 L11 7.5 L11 10 C11 10.6 10.5 11 10 11 C5 10.6 1.4 7 1 2 C1 1.5 1.4 1 2 1 Z"/></svg>
      <span>+555 2540-3367</span>
    </li>
    <li class="contact__item">
      <svg class="contact__icon" viewBox="0 0 12 12" aria-hidden="true"><path d="M1 2.5 L11 2.5 L11 9.5 L1 9.5 Z M1.8 3.2 L6 6.3 L10.2 3.2" stroke="var(--maroon)" stroke-width="0.8"/></svg>
      <span>info@martinhalloway.com</span>
    </li>
  </ul>

  <p class="address">42 Alder Lane Northfield, Ohio 44067</p>
</section>

<section class="card card--back" aria-label="Card back">
  <div class="brand"><span class="brand__dot"></span><span>Bastion Guard<br>Systems Inc.</span></div>
  <p class="website">www.bastionguardsystems.com</p>
</section>

</body>
</html>
```